Business card for Sports Apparel business

DOUBLE SIDED DESIGN
We need business cards for a new sports apparel business. We are developing a protective headband for soccer initially.
Torvalle is focused on designing and developing head protection products to reduce the likelihood of concussion when playing sports. Exploring and understanding medical insights, material science research, current and former players experiences and governing bodies guidelines has allowed Torvalle to develop the safety, style, form and function requirements of a suitable product to bring to market.
Target Market(s)
Mums buying kits for the sons and daughters. Amateur footballers.
Industry/Entity Type
Sporting Good
Contact Information for Business Card
Martin Ashworth - CEO
Mobile: +44 7431589027
Email: martin@torvalle.co.uk
Tel: 0208 5519372
Helena Pargeter - COO
Mob: +44 7385 640117
Email: helena@torvalle.co.uk
Tel: 0208 5519372
Duncan Farrow - CCO
Mob: +44 7564 293081
Email: duncan@torvalle.co.uk
Tel: 0208 5519372
Look and feel
Each slider illustrates characteristics of the customer's brand and the style your logo design should communicate.

```html
<!DOCTYPE html>
<html lang="en">
<head>
<meta charset="utf-8">
<title>Torvalle — Business Card</title>
<link rel="stylesheet" href="https://fonts.googleapis.com/css2?family=Montserrat:wght@400;500&display=swap">
<style>
  :root {
    --page: #e6e7e9;
    --card-white: #fbfbfb;
    --card-black: #0d0d0e;
    --brand-blue: #1a82c4;
    --ink-grey: #8a8d91;
    --logo-grey: #6f7276;
  }
  * { box-sizing: border-box; margin: 0; padding: 0; }
  html, body { width: 1200px; height: 1023px; overflow: hidden; }
  body {
    background: var(--page);
    font-family: "Montserrat", sans-serif;
    position: relative;
  }
  .card {
    position: absolute;
    left: 320px;
    width: 560px;
    height: 340px;
    border-radius: 3px;
    box-shadow: 0 6px 18px rgba(0,0,0,.18);
    overflow: hidden;
  }
  .card--front { top: 140px; background: var(--card-white); }
  .card--back { top: 543px; background: var(--card-black); }

  .brand-mark {
    position: absolute;
    left: 48px;
    top: 150px;
    display: flex;
    align-items: center;
    gap: 10px;
  }
  .brand-mark__square {
    width: 14px; height: 14px;
    background: var(--brand-blue);
  }
  .brand-mark__name {
    font-weight: 500;
    font-size: 30px;
    letter-spacing: 3px;
    color: var(--brand-blue);
    text-transform: uppercase;
  }

  .divider {
    position: absolute;
    left: 268px;
    width: 1.5px;
    background: var(--brand-blue);
  }
  .divider--top { top: 62px; height: 66px; }
  .divider--bottom { top: 178px; height: 100px; }

  .contact {
    position: absolute;
    left: 296px;
    top: 70px;
  }
  .contact__name {
    font-weight: 500;
    font-size: 19px;
    letter-spacing: 1px;
    color: var(--brand-blue);
    text-transform: uppercase;
  }
  .contact__role {
    font-size: 12px;
    color: var(--ink-grey);
    letter-spacing: 1px;
    margin-top: 4px;
  }
  .contact__list {
    list-style: none;
    margin-top: 22px;
  }
  .contact__item {
    display: flex;
    align-items: center;
    gap: 10px;
    font-size: 12.5px;
    color: var(--ink-grey);
    line-height: 22px;
    letter-spacing: .4px;
  }
  .contact__icon { width: 12px; height: 12px; flex: none; }

  .back-field {
    position: absolute; inset: 0;
    background: linear-gradient(125deg, #0a0a0b 0%, #161718 45%, #4a4c4f 75%, #1c1d1f 100%);
  }
  .back-name {
    position: absolute;
    left: 0; right: 0;
    top: 150px;
    text-align: center;
    font-weight: 500;
    font-size: 30px;
    letter-spacing: 3px;
    color: var(--brand-blue);
    text-transform: uppercase;
  }
</style>
</head>
<body>
  <section class="card card--front" aria-label="Card front">
    <div class="brand-mark">
      <span class="brand-mark__square"></span>
      <span class="brand-mark__name">Torvalle</span>
    </div>

    <span class="divider divider--top"></span>
    <span class="divider divider--bottom"></span>

    <div class="contact">
      <p class="contact__name">Martin Ashworth</p>
      <p class="contact__role">CEO</p>
      <ul class="contact__list">
        <li class="contact__item">
          <svg class="contact__icon" viewBox="0 0 12 12" aria-hidden="true"><path d="M3 1 L5 3.5 L4 5 Q5 7 7 8 L8.5 7 L11 9 L9.5 11 Q4 10.5 1 3 Z" fill="none" stroke="#1a82c4" stroke-width="1"/></svg>
          0208 5519372
        </li>
        <li class="contact__item">
          <svg class="contact__icon" viewBox="0 0 12 12" aria-hidden="true"><rect x="3" y="1" width="6" height="10" rx="1" fill="none" stroke="#1a82c4" stroke-width="1"/><line x1="5" y1="9.3" x2="7" y2="9.3" stroke="#1a82c4"/></svg>
          +44 7431589027
        </li>
        <li class="contact__item">
          <svg class="contact__icon" viewBox="0 0 12 12" aria-hidden="true"><rect x="1" y="2.5" width="10" height="7" fill="none" stroke="#1a82c4" stroke-width="1"/><path d="M1 2.5 L6 6.5 L11 2.5" fill="none" stroke="#1a82c4" stroke-width="1"/></svg>
          martin@torvalle.co.uk
        </li>
        <li class="contact__item">
          <svg class="contact__icon" viewBox="0 0 12 12" aria-hidden="true"><circle cx="6" cy="6" r="5" fill="none" stroke="#1a82c4"/><ellipse cx="6" cy="6" rx="2.2" ry="5" fill="none" stroke="#1a82c4" stroke-width=".8"/><line x1="1" y1="6" x2="11" y2="6" stroke="#1a82c4" stroke-width=".8"/></svg>
          www.torvalle.co.uk
        </li>
      </ul>
    </div>
  </section>

  <section class="card card--back" aria-label="Card back">
    <div class="back-field" role="img" aria-label="Dark repeating diagonal brand-name pattern with a grey sheen"></div>
    <p class="back-name">Torvalle</p>
  </section>
</body>
</html>
```